Web site for radio show

I've got a radio show starting on OrbitalWave and need a web site for it. I am familiar with WordPress, so I'd like to get a design for a WordPress-based web site for the show.

I'm also posting a logo project to be done at the same time.

The best radio show web site I've seen is the Cosmic Tuesday site (www.cosmictuesday-example.com). That's a good model but I don't want to start with that much complexity and content. The initial site that I'd like you to design would have the following parts:
- Upcoming shows
- Past shows (including links to authors, their web sites, and their books)
- Twitter feed
- Blog
- About
- ...and anything else you think would be necessary

For colors, I'd like it to be consistent with my personal web site: www.kellaway-ventures-example.com

Target Market(s)

The target market for this show is mid- to upper-level managers

Industry/Entity Type

Radio

Requirements
Must have
• The project has to proceed in (at least) two stages: a first rough layout, and a second finished design. Whether you want a third stage in between with look and feel options is up to you.

```html
<!DOCTYPE html>
<html lang="en">
<head>
<meta charset="utf-8">
<title>Kellaway Show</title>
<link rel="stylesheet" href="https://fonts.googleapis.com/css2?family=Open+Sans:wght@400;600;700&display=swap">
<style>
:root{
  --red:#9c1a1f;
  --red-dark:#7d1216;
  --page:#ececec;
  --panel:#ffffff;
  --ink:#333333;
  --muted:#7a7a7a;
  --rule:#dddddd;
  --footer:#2b2b2b;
  --footer-text:#9a9a9a;
}
*{box-sizing:border-box;margin:0;padding:0}
html,body{width:872px;height:1200px;overflow:hidden}
body{font-family:"Open Sans",Arial,sans-serif;color:var(--ink);background:var(--page)}
.page{width:872px;height:1200px;display:flex;flex-direction:column;overflow:hidden}

.masthead{height:86px;flex:none;background:linear-gradient(180deg,#ab1f25,var(--red-dark));display:flex;align-items:center;justify-content:space-between;padding:0 38px}
.brand{color:#fff;font-size:25px;font-weight:700;letter-spacing:.2px}
.social{display:flex;gap:9px}
.social span{width:22px;height:22px;border-radius:50%;border:2px solid rgba(255,255,255,.85)}

.main-nav{height:36px;flex:none;background:var(--panel);display:flex;align-items:center;padding:0 38px;box-shadow:0 1px 2px rgba(0,0,0,.12)}
.main-nav a{font-size:12px;font-weight:700;color:var(--ink);text-decoration:none;padding:0 15px;border-right:1px solid var(--rule);line-height:14px}
.main-nav a:first-child{padding-left:0}
.main-nav a:last-child{border-right:0}

.content{padding:0 38px}
.hero{margin-top:18px;height:252px;position:relative;background:radial-gradient(circle at 74% 40%,#e8e8e8 0,#9a9a9a 18%,#3a3a3a 45%,#1c1c1c 100%)}
.hero-title{position:absolute;left:40px;top:132px;color:#fff;font-size:22px;font-weight:600}
.hero-dots{position:absolute;left:50%;bottom:14px;transform:translateX(-50%);display:flex;gap:6px}
.hero-dots i{width:8px;height:8px;border-radius:50%;background:rgba(255,255,255,.5)}
.hero-dots i:first-child{background:#fff}

.welcome{margin-top:14px;height:185px;background:var(--panel);display:flex}
.welcome-icon{width:180px;flex:none;background:#d8d8d8;display:flex;align-items:center;justify-content:center}
.welcome-body{padding:14px 16px;display:flex;flex-direction:column}
.welcome-body h1{font-size:14px;font-weight:600;margin-bottom:8px}
.welcome-body p{font-size:10.5px;line-height:17px;color:var(--muted)}
.read-more{align-self:flex-end;margin-top:auto;font-size:10px;color:var(--ink)}

.shows{margin-top:18px;height:233px;display:flex;gap:16px}
.section-title{font-size:14px;font-weight:600;margin-bottom:8px;height:20px}
.upcoming{width:410px;flex:none}
.upcoming-grid{display:flex;gap:12px}
.show-card{width:199px}
.photo{display:block}
.photo-studio{height:116px;background:linear-gradient(135deg,#c89a5a,#7a5534)}
.photo-host{height:116px;background:linear-gradient(135deg,#5a6f86,#2d3b4a)}
.photo-mic{height:80px;margin-top:9px;background:linear-gradient(135deg,#b8b8b8,#4a4a4a)}
.show-card h3{font-size:11px;font-weight:600;margin-top:7px}
.show-meta{font-size:8.5px;color:var(--muted);margin-top:2px}
.show-card p{font-size:9px;line-height:13px;color:var(--muted);margin-top:3px}
.show-card .more{font-size:9px;font-weight:700;color:var(--ink)}
.past{flex:1}
.photo-concert{height:150px;background:linear-gradient(180deg,#3c4f8a,#c47a3a 70%,#2a2a2a)}
.past-caption{height:55px;background:var(--panel);display:flex;align-items:center;justify-content:space-between;padding:0 14px}
.past-caption h3{font-size:12px;font-weight:600}
.past-icons{display:flex;gap:8px}

.feeds{margin-top:14px;height:244px;display:flex;gap:16px}
.feed-panel{flex:1;background:var(--panel)}
.feed-head{height:44px;border-bottom:1px solid var(--rule);display:flex;align-items:center;gap:12px;padding:0 14px}
.feed-mark{width:24px;height:24px;background:var(--red)}
.feed-head h2{font-size:12px;font-weight:600;letter-spacing:.3px}
.tweet{display:flex;gap:12px;padding:12px 14px 0}
.tweet-mark{width:18px;height:18px;background:var(--red);flex:none;margin-top:2px}
.tweet p{font-size:9px;line-height:13px;color:var(--muted)}
.tweet .handle{color:var(--ink)}
.blog-post{padding:16px 18px;display:flex;gap:12px}
.quote{font-size:34px;line-height:28px;color:var(--ink);font-weight:700}
.blog-post p{font-size:10px;line-height:15px;color:var(--muted)}
.author{display:flex;align-items:center;gap:12px;padding:2px 18px 0 60px}
.avatar{width:50px;height:50px;border-radius:50%;background:#b9b9b9;flex:none}
.author h4{font-size:11px;font-weight:600}
.author span{display:block;font-size:9px;color:var(--muted);line-height:13px}

.site-footer{margin-top:auto;height:85px;flex:none;background:var(--footer);display:flex;align-items:center;justify-content:space-between;padding:0 38px}
.footer-links{display:flex;gap:14px;font-size:9.5px;color:#cfcfcf}
.copyright{font-size:9px;color:var(--footer-text);margin-top:6px}
.partner{display:flex;align-items:center;gap:8px;color:#fff;font-size:18px;font-weight:700}
.partner i{width:16px;height:16px;border-radius:50%;background:#3a8fd8}
</style>
</head>
<body>
<div class="page">
  <header class="masthead">
    <div class="brand">Kellaway Show</div>
    <div class="social"><span></span><span></span><span></span><span></span><span></span></div>
  </header>
  <nav class="main-nav">
    <a href="#">Home</a><a href="#">About</a><a href="#">Upcoming shows</a><a href="#">Past shows</a><a href="#">Radio show</a><a href="#">Blog</a><a href="#">Contact Us</a>
  </nav>

  <main class="content">
    <section class="hero" role="img" aria-label="Studio microphone with bright light in a dark room">
      <div class="hero-title">Kellaway Show</div>
      <div class="hero-dots"><i></i><i></i><i></i></div>
    </section>

    <section class="welcome">
      <div class="welcome-icon">
        <svg width="70" height="90" viewBox="0 0 70 90" aria-hidden="true">
          <rect x="22" y="4" width="26" height="46" rx="13" fill="#8a8a8a"/>
          <path d="M12 36 v4 a23 23 0 0 0 46 0 v-4" fill="none" stroke="#8a8a8a" stroke-width="5"/>
          <rect x="32" y="63" width="6" height="14" fill="#8a8a8a"/>
          <rect x="18" y="77" width="34" height="6" fill="#8a8a8a"/>
        </svg>
      </div>
      <div class="welcome-body">
        <h1>Welcome To Kellaway Show</h1>
        <p>Each week we sit down with leaders, authors and managers who shape how organizations work. Our conversations cover strategy, decision making, culture, teams and the books behind the ideas. Listen live, catch up on past shows, read the blog and follow along as new guests join the program. Every episode aims to give busy managers practical insight they can use on Monday morning, with links to guest websites and their latest books so you can keep learning after the show ends.</p>
        <a class="read-more">Read More</a>
      </div>
    </section>

    <section class="shows">
      <div class="upcoming">
        <h2 class="section-title">Upcoming shows</h2>
        <div class="upcoming-grid">
          <article class="show-card">
            <div class="photo photo-studio" role="img" aria-label="Radio studio mixing desk"></div>
            <h3>Elementum mauris aliquet ut</h3>
            <div class="show-meta">July 18, 2014 | 2 Comments</div>
            <p>A candid talk on leading through change, with a guest whose new book looks at how teams adapt. <span class="more">More...</span></p>
          </article>
          <div class="show-card">
            <div class="photo photo-host" role="img" aria-label="Host wearing headphones at the microphone"></div>
            <div class="photo photo-mic" role="img" aria-label="Close view of a studio microphone"></div>
          </div>
        </div>
      </div>
      <div class="past">
        <h2 class="section-title">Past shows</h2>
        <div class="photo photo-concert" role="img" aria-label="Crowd in front of a lit stage"></div>
        <div class="past-caption">
          <h3>Elementum mauris</h3>
          <div class="past-icons">
            <svg width="14" height="14" viewBox="0 0 14 14" aria-hidden="true"><circle cx="7" cy="4" r="3" fill="#555"/><path d="M1 14 a6 6 0 0 1 12 0z" fill="#555"/></svg>
            <svg width="14" height="14" viewBox="0 0 14 14" aria-hidden="true"><rect x="1" y="2" width="12" height="11" fill="none" stroke="#555" stroke-width="2"/><rect x="1" y="2" width="12" height="3" fill="#555"/></svg>
            <svg width="14" height="14" viewBox="0 0 14 14" aria-hidden="true"><rect x="2" y="1" width="10" height="12" fill="none" stroke="#555" stroke-width="2"/><path d="M4.5 5h5M4.5 8h5" stroke="#555" stroke-width="1.5"/></svg>
          </div>
        </div>
      </div>
    </section>

    <section class="feeds">
      <div class="feed-panel">
        <div class="feed-head"><span class="feed-mark"></span><h2>LATEST TWEETS</h2></div>
        <div class="tweet"><span class="tweet-mark"></span><p><span class="handle">@kellawayshow</span><br>Fresh episode notes are up, with links to this week's guest and book.<br>11/08/2013, 12:59</p></div>
        <div class="tweet"><span class="tweet-mark"></span><p><span class="handle">@kellawayshow</span><br>Tune in Thursday for a conversation on hiring well and building teams.<br>11/08/2013, 12:59</p></div>
        <div class="tweet"><span class="tweet-mark"></span><p><span class="handle">@kellawayshow</span><br>Thanks to everyone who called in today, more listener questions next week.<br>11/08/2013, 12:59</p></div>
      </div>
      <div class="feed-panel">
        <div class="feed-head"><span class="feed-mark"></span><h2>LATEST BLOG POSTS</h2></div>
        <div class="blog-post">
          <span class="quote">&ldquo;</span>
          <p>Many managers ask how to keep meetings short and useful. This week we share three habits from our guests that help teams decide faster and follow through.</p>
        </div>
        <div class="author">
          <div class="avatar" role="img" aria-label="Host portrait"></div>
          <div><h4>Kellaway Show</h4><span>Host, Weekly Leadership Radio</span><span>posted 2 days ago</span></div>
        </div>
      </div>
    </section>
  </main>

  <footer class="site-footer">
    <div>
      <div class="footer-links"><span>Contact</span><span>Supporters</span><span>Newsletter</span><span>Policies</span><span>Available from TuneHarbor</span></div>
      <div class="copyright">&copy; 2014 Kellaway Show. All rights reserved.</div>
    </div>
    <div class="partner"><i></i>OrbitalWave</div>
  </footer>
</div>
</body>
</html>
```